Lotstallmart.com Webpage Design

Design Brief for lotstallmart.com (Copy of Brief also in attached Word file)

Name of Website- lotstallmart.com (existing logo and look & feel of website to be changed)

Logo - Finalised. The logo files are attached with the brief as “logo.jpeg”. The “Blue- Grey” version of the logo is for use on lighter backgrounds and the “Orange-White” version of the logo is for use on darker backgrounds. (A full Black version of the logo is also attached). Both versions may be used in different parts of the website. All attached files are in .png format.
Status - The website in functional and is undergoing user trials. However, we want to improve the look & feel of the website so at it seems
a. cotemporary,
b. Easy to Navigate
c. professional and
d. Vibrant.

Please visit ‘lotstallmart.com’ to check out the website and its functionalities – please use it only as a reference for the features & functions to be provided, however the designer should use a ‘Free Hand’ in designing the composition of various parts of the webpage without getting too influenced by the existing design

Objective of the Website ‘lotstallmart.com –
a. It is a portal focussed on listing of ‘Retail’ specific real-estate properties by developers, owners and realty brokers. The properties shall listed under the following four categories-
i. Retail Malls
ii. Shopping Complexes
iii. High-street shops
iv. Retail Warehouses
*refer lotstallmart.com for better clarity

b. The abovementioned properties shall be listed either for ‘Sale’ or ‘rent\lease’ or both

c. Users shall visit the site in case they wish to acquire a retail \ shop space either on ‘sale’ or ‘rent’. These Users would be able to specify the ‘Search Criteria’ through the tool-bars provided on the website – the ‘Search Criteria’ shall comprise of ‘Type of space category’, ‘City’, ‘Locality’, transaction type ie ‘Rent \ Sale’ and ‘Area Range’

d. The main revenue model for the website shall be listing fee ( or advertising charges ) payable by those listing their properties on the website.

Three Main Pages of Website (lotstallmart.com) that need to be designed -
a. Main Home Page (visit the web link - http://lotstallmart.com/ ) - The main home page has the “Search Toolbar” for specifying of Search Criteria by the User. It shall also have the following features & functions-
i. Main Advertising Banner
ii. Featured Projects
iii. New Launches
iv. Toolbar with buttons – ‘Advertise with Us’, ‘Listings Alert’, ‘Mart Wizards’, ‘Advertiser Login’

b. Property Listings Page (visit the web link - http://lotstallmart.com/gurgaon-in-india ) - The List of property options that match the Criteria specified by the ‘User’ get displayed on this page.

c. Property Detail Page - When the ‘User’ clicks on the “More….” Button on the ‘Property Listings Page’ (given in point b. above) the web page with the details of the property opens. (For Example – visit the web link - http://lotstallmart.com/vorne-Shopping-Complex-vorne-quadrion-gurgaon-636 )

Note:- Please refer to attached ‘Shopping’ related images the designer may use them on the website to provide a look & feel of retail if required – either separately or rotate in a single window

Target Market(s)

Retailers & Investors looking for retail space, Real Estate Brokers, Developers

Industry/Entity Type

Advertising

Number of Pages Required

3 page

Requirements
Must have
• Refer to existing site lotstallmart.com -- all the existing functionalities are a must have.
Nice to have
• The Designer may use the retail related images on the website if required for making it more vibrant. Refer attached images Shopping(1-6).jpg

```html
<!DOCTYPE html>
<html lang="en">
<head>
<meta charset="utf-8">
<title>Lotstallmart.com – Retail Space Portal</title>
<link href="https://fonts.googleapis.com/css2?family=Oxygen:wght@300;400;700&display=swap" rel="stylesheet">
<style>
:root{
  --blue:#0a9cf0;
  --blue-dark:#0786d1;
  --orange:#ff9a00;
  --ink:#222;
  --grey:#666;
  --line:#d6d6d6;
  --white:#fff;
}
*{box-sizing:border-box;margin:0;padding:0}
html,body{width:1200px;height:3468px;overflow:hidden}
body{position:relative;background:var(--white);font-family:"Oxygen",Arial,sans-serif;color:var(--ink)}
.abs{position:absolute}
a{color:inherit;text-decoration:none}

/* top city strip */
.city-strip{left:0;top:0;width:1200px;height:24px;background:rgba(15,12,10,.8);z-index:3;display:flex;justify-content:center;gap:22px;align-items:center;font-size:9px;letter-spacing:.5px;color:#bbb}

/* hero: warm shopping-arcade tones */
.hero{left:0;top:0;width:1200px;height:631px;
  background:
    radial-gradient(ellipse 220px 160px at 640px 120px,rgba(255,214,140,.75),rgba(255,214,140,0)),
    radial-gradient(ellipse 200px 130px at 980px 90px,rgba(255,226,170,.6),rgba(255,226,170,0)),
    radial-gradient(ellipse 160px 120px at 120px 150px,rgba(255,200,120,.5),rgba(255,200,120,0)),
    radial-gradient(ellipse 110px 190px at 520px 330px,rgba(230,230,235,.55),rgba(230,230,235,0)),
    radial-gradient(ellipse 90px 170px at 750px 330px,rgba(210,90,60,.55),rgba(210,90,60,0)),
    radial-gradient(ellipse 70px 110px at 590px 430px,rgba(70,140,220,.55),rgba(70,140,220,0)),
    radial-gradient(ellipse 260px 200px at 1080px 330px,rgba(60,120,110,.45),rgba(60,120,110,0)),
    linear-gradient(180deg,#4a3a2c 0%,#7a5e40 30%,#6b5038 55%,#8a6a48 75%,#5a4630 100%)}
.brand{left:92px;top:50px;display:flex;align-items:center;gap:8px;color:var(--white);font-weight:700;font-size:29px;z-index:3}
.brand .dot{width:34px;height:34px;border-radius:50%;background:var(--white)}
.main-nav{left:436px;top:63px;display:flex;gap:6px;font-size:12px;font-weight:700;color:var(--white);z-index:3}
.main-nav a{height:22px;line-height:22px;padding:0 8px}
.main-nav .current{background:var(--blue)}
.main-nav .login{background:var(--orange);margin-left:8px}
.main-nav .register{background:rgba(120,120,120,.75)}

.search-panel{left:88px;top:178px;width:257px;height:384px;background:var(--white);padding:22px 20px;box-shadow:0 2px 12px rgba(0,0,0,.3)}
.search-panel h2{font-size:17px;text-align:center;font-weight:700}
.search-panel .meaning{font-size:9px;text-align:center;margin:6px 0 12px}
.formats{display:grid;grid-template-columns:1fr 1fr;gap:6px 8px;font-size:9px;color:var(--grey);margin-bottom:10px}
.formats span::before{content:"";display:inline-block;width:8px;height:8px;border:1px solid #aaa;margin-right:4px;vertical-align:-1px}
.field{height:26px;border:1px solid #ccc;font-size:9px;color:#777;padding:0 8px;line-height:24px;margin-bottom:9px;position:relative}
.field.keyword{border-color:var(--blue);color:var(--blue)}
.field.select::after{content:"";position:absolute;right:8px;top:8px;width:5px;height:5px;border-right:1.5px solid #555;border-bottom:1.5px solid #555;transform:rotate(45deg)}
.search-btn{height:37px;background:var(--orange);color:var(--white);font-weight:700;font-size:13px;text-align:center;line-height:37px;margin-top:4px}

.hero-caption{left:697px;top:404px;width:503px}
.hero-caption h1{font-size:21px;font-weight:700;color:var(--white);text-shadow:0 1px 3px rgba(0,0,0,.5)}
.hero-caption p{margin-top:10px;font-size:13px;color:var(--white);text-shadow:0 1px 3px rgba(0,0,0,.5)}
.start-btn{left:673px;top:477px;width:150px;height:34px;background:var(--blue);color:var(--white);font-size:13px;font-weight:700;line-height:34px;padding-left:26px}
.slider-dots{left:676px;top:543px;display:flex;gap:3px}
.slider-dots i{width:9px;height:9px;border-radius:50%;border:1px solid var(--white)}
.slider-dots i.on{background:var(--white)}

/* category band */
.category-band{left:0;top:631px;width:1200px;height:90px;background:var(--blue);display:flex;justify-content:center;gap:70px;align-items:center;color:var(--white);font-size:13px;font-weight:700;line-height:16px}
.category-band .cat{display:flex;align-items:center;gap:12px}
.cat .ring{width:46px;height:46px;border-radius:50%;border:2px solid var(--white);display:flex;align-items:center;justify-content:center}

/* intro */
.intro{left:170px;top:786px;width:860px;font-size:16px;line-height:22px;text-align:center}

/* tabs */
.tab{top:929px;width:247px;height:34px;line-height:34px;text-align:center;font-size:13px;font-weight:700}
.tab.active{left:349px;background:var(--blue);color:var(--white)}
.tab.active::after{content:"";position:absolute;left:116px;bottom:-7px;border:7px solid transparent;border-bottom:0;border-top-color:var(--blue)}
.tab.idle{left:606px;border:2px solid var(--line);color:#aaa;font-weight:400}
.tab-sub{top:980px;width:247px;font-size:10px;color:var(--grey);text-align:center;display:flex;align-items:center;gap:8px;justify-content:center}
.tab-sub::before,.tab-sub::after{content:"";width:48px;height:1px;background:#999}

/* project cards */
.card{width:264px}
.card .photo{width:264px;height:264px;position:relative;overflow:hidden}
.card .photo .name{position:absolute;left:0;bottom:0;width:100%;height:50px;background:rgba(0,0,0,.55);color:var(--white);font-size:16px;text-align:center;line-height:50px}
.card h3{margin-top:18px;font-size:13px;font-weight:700}
.card .loc{margin-top:10px;font-size:11px;display:flex;align-items:center;gap:5px}
.card .view{margin-top:10px;font-size:10px;color:var(--blue)}

/* mart wizards */
.wizards-photo{left:0;top:1926px;width:557px;height:261px;
  background:
    radial-gradient(ellipse 160px 110px at 90px 80px,rgba(120,150,190,.55),rgba(120,150,190,0)),
    radial-gradient(ellipse 200px 90px at 420px 60px,rgba(150,170,200,.45),rgba(150,170,200,0)),
    linear-gradient(180deg,#3c4c62 0%,#2d3a4c 45%,#252d38 100%)}
.wizards-copy{left:60px;top:1998px;width:440px;text-align:center;color:var(--white)}
.wizards-copy h2{font-size:21px;font-weight:700}
.wizards-copy p{margin-top:14px;font-size:14px;line-height:19px}
.wizards-copy .rule{width:28px;height:3px;background:var(--white);margin:12px auto 0}
.wizards-form{left:557px;top:1926px;width:643px;height:261px;background:var(--orange)}
.in{background:var(--white);font-size:11px;color:#888;padding:0 10px;line-height:35px;height:39px;border:1px solid #fff}
.in.email{left:592px;top:1979px;width:254px;border:2px solid var(--blue);color:var(--blue)}
.in.mobile{left:855px;top:1979px;width:255px}
.in.message{left:592px;top:2025px;width:518px;height:77px;line-height:26px}
.send-btn{left:592px;top:2111px;width:97px;height:35px;border:2px solid var(--white);color:var(--white);font-weight:700;font-size:13px;line-height:31px;padding-left:22px}

/* alert + editor boxes */
.info-box{top:2252px;width:343px;height:492px;background:var(--blue);color:var(--white);text-align:center}
.info-box h2{margin-top:52px;font-size:22px;font-weight:700}
.alert-box{left:254px}
.editor-box{left:601px;width:342px}
.alert-box .lead{font-size:11px;line-height:15px;margin:26px auto 0;width:260px}
.box-field{position:absolute;left:46px;width:259px;height:35px;background:var(--white);color:#777;font-size:11px;text-align:left;padding-left:12px;line-height:33px}
.box-field.select::after{content:"";position:absolute;right:12px;top:11px;width:6px;height:6px;border-right:1.5px solid #555;border-bottom:1.5px solid #555;transform:rotate(45deg)}
.box-field.first{border:2px solid #0568a8}
.hint{position:absolute;left:46px;font-size:8px;color:#cfe9ff;text-align:left}
.box-btn{position:absolute;height:34px;border:2px solid var(--white);font-size:13px;font-weight:700;line-height:30px}
.editor-box .pic{position:absolute;left:35px;top:106px;width:277px;height:162px;
  background:
    radial-gradient(ellipse 90px 110px at 150px 90px,rgba(255,255,255,.95),rgba(255,255,255,0)),
    radial-gradient(ellipse 60px 80px at 200px 110px,rgba(90,130,180,.55),rgba(90,130,180,0)),
    linear-gradient(180deg,#6fa7de 0%,#a9cdee 45%,#d8e4ee 75%,#8a9aaa 100%)}
.editor-box .copy{position:absolute;left:30px;top:286px;width:282px;font-size:11px;line-height:15px}

/* footer: evening street tones */
.footer{left:0;top:2767px;width:1200px;height:701px;
  background:
    radial-gradient(ellipse 90px 170px at 200px 390px,rgba(200,150,50,.55),rgba(200,150,50,0)),
    radial-gradient(ellipse 80px 160px at 310px 360px,rgba(170,60,40,.5),rgba(170,60,40,0)),
    radial-gradient(ellipse 80px 160px at 880px 360px,rgba(140,50,40,.45),rgba(140,50,40,0)),
    radial-gradient(ellipse 70px 170px at 1080px 400px,rgba(60,60,70,.6),rgba(60,60,70,0)),
    radial-gradient(ellipse 220px 120px at 700px 90px,rgba(90,140,170,.45),rgba(90,140,170,0)),
    linear-gradient(180deg,#3c4650 0%,#2f353c 40%,#40403e 75%,#2a2c2e 100%)}
.footer-brand{left:0;top:2960px;width:1200px;display:flex;justify-content:center;align-items:center;gap:8px;color:var(--white);font-size:20px;font-weight:700}
.footer-brand .dot{width:24px;height:24px;border-radius:50%;background:var(--white)}
.footer-brand::before,.footer-brand::after{content:"";width:130px;height:1px;background:rgba(255,255,255,.6);margin:0 10px}
.footer-links{left:0;width:1200px;display:flex;justify-content:center;gap:26px;font-size:12px;color:var(--white)}
.footer-links .hl{color:var(--blue)}
.thumbs{left:325px;top:3153px;display:flex;gap:13px}
.thumb{width:77px;text-align:center;font-size:10px;color:#ddd}
.thumb .pic{height:58px;border:2px solid var(--white);margin-bottom:6px}
.footer-bottom{left:0;top:3375px;width:1200px;height:93px;background:rgba(0,0,0,.3)}
.address{left:130px;top:3390px;font-size:12px;line-height:20px;color:var(--white);font-style:normal}
.socials{left:590px;top:3400px;display:flex;gap:14px}
.socials i{width:18px;height:18px;border-radius:50%;background:var(--white)}
.copyright{right:90px;top:3390px;font-size:12px;line-height:20px;color:var(--white);text-align:right}
</style>
</head>
<body>

<!-- hero -->
<div class="abs hero" role="img" aria-label="Photo of a smiling family walking through a brightly lit shopping arcade carrying shopping bags"></div>
<div class="abs city-strip">
  <span>BANGALORE</span><span>CHENNAI</span><span>GREATER NOIDA</span><span>GURGAON</span><span>HYDERABAD</span><span>JAIPUR</span><span>KHANNA</span><span>KOLKATA</span><span>MUMBAI</span><span>NOIDA</span><span>PUNE</span><span>SURAT</span>
</div>
<div class="abs brand"><span class="dot"></span>lotstallmart</div>
<nav class="abs main-nav">
  <a class="current">Home</a><a>Advertise with Us</a><a>Mart Wizards</a><a>Listing Alert</a>
  <a class="login">Advertiser Login</a><a class="register">New Advertiser - Register</a>
</nav>

<form class="abs search-panel">
  <h2>Select Retail Format</h2>
  <p class="meaning">› Meaning of Retail Format</p>
  <div class="formats">
    <span>Retail Malls</span><span>High Street Shops</span>
    <span>Shopping Complex</span><span>Retail Warehouses</span>
  </div>
  <div class="field keyword">Enter Keywords</div>
  <div class="field select">Sale Or Rent Or Both</div>
  <div class="field select">Select City</div>
  <div class="field select">Select Locality/Micro Market</div>
  <div class="field select">Select Locality/Micro Market</div>
  <div class="search-btn">SEARCH NOW ⌕</div>
</form>

<div class="abs hero-caption">
  <h1>Shops at Cox Town Bangalore</h1>
  <p>Lorem ipsum dolor sit amet, consectetur adipisicing elit</p>
</div>
<a class="abs start-btn">Get Started ›</a>
<div class="abs slider-dots"><i class="on"></i><i></i><i></i><i></i></div>

<!-- categories -->
<div class="abs category-band">
  <div class="cat"><span class="ring"><svg width="22" height="22" viewBox="0 0 22 22" fill="none" stroke="#fff" stroke-width="1.6"><path d="M3 9h16M4 9v10h14V9M2 9l9-6 9 6M8 19v-5h6v5"/></svg></span>Retail<br>Malls</div>
  <div class="cat"><span class="ring"><svg width="22" height="22" viewBox="0 0 22 22" fill="none" stroke="#fff" stroke-width="1.6"><rect x="4" y="3" width="14" height="16"/><path d="M7 7h3M12 7h3M7 11h3M12 11h3M9 19v-4h4v4"/></svg></span>Shopping<br>Complexes</div>
  <div class="cat"><span class="ring"><svg width="22" height="22" viewBox="0 0 22 22" fill="none" stroke="#fff" stroke-width="1.6"><path d="M5 8h12l-1 11H6z"/><path d="M8 8V6a3 3 0 0 1 6 0v2"/></svg></span>High-Street<br>Shops</div>
  <div class="cat"><span class="ring"><svg width="22" height="22" viewBox="0 0 22 22" fill="none" stroke="#fff" stroke-width="1.6"><path d="M2 5h3l2 10h11l2-7H6"/><circle cx="9" cy="18" r="1.3"/><circle cx="16" cy="18" r="1.3"/></svg></span>Retail<br>Warehouses</div>
</div>

<p class="abs intro">LotStallMart.com is a Specialised Web based platform for Retail Space, featuring properties across India under various formats such as Retail Malls, Shopping Complexes, High-street Shops. Also featured are Retail Warehouses which provide the logistic back-end for the retail business. LotStallMart.com is useful to various category of users as follows- a. Devel</p>

<div class="abs tab active">Featured Retail Projects</div>
<div class="abs tab idle">Featured New Launches</div>
<div class="abs tab-sub" style="left:349px">Across India</div>
<div class="abs tab-sub" style="left:606px;color:#aaa">Across India</div>

<!-- featured projects row 1 -->
<article class="abs card" style="left:60px;top:1070px">
  <div class="photo" role="img" aria-label="Photo of a beige shopping complex with arched windows under a clear sky" style="background:radial-gradient(ellipse 150px 70px at 132px 170px,rgba(220,190,140,.9),rgba(220,190,140,0)),radial-gradient(ellipse 80px 40px at 132px 205px,rgba(60,110,70,.7),rgba(60,110,70,0)),linear-gradient(180deg,#8fbde4 0%,#c4d9ea 32%,#d6c29a 48%,#b79a6e 70%,#6e6a5a 100%)"><span class="name">Magnora</span></div>
  <h3>Shopping Complex</h3>
  <p class="loc"><svg width="9" height="12" viewBox="0 0 9 12"><path d="M4.5 0A4.5 4.5 0 0 0 0 4.5C0 8 4.5 12 4.5 12S9 8 9 4.5A4.5 4.5 0 0 0 4.5 0z" fill="#222"/><circle cx="4.5" cy="4.5" r="1.6" fill="#fff"/></svg>Surat - Althan</p>
  <p class="view" style="color:var(--orange)">› View the Listing</p>
</article>
<article class="abs card" style="left:333px;top:1070px">
  <div class="photo" role="img" aria-label="Photo of a high street building lit up at dusk with palm trees" style="background:radial-gradient(ellipse 120px 60px at 140px 120px,rgba(255,200,110,.85),rgba(255,200,110,0)),radial-gradient(ellipse 60px 50px at 60px 190px,rgba(40,90,60,.8),rgba(40,90,60,0)),radial-gradient(ellipse 60px 50px at 210px 190px,rgba(40,90,60,.8),rgba(40,90,60,0)),linear-gradient(180deg,#1f3358 0%,#3a4c72 35%,#8a7458 60%,#4a4238 100%)"><span class="name">Vireo 81 High Street</span></div>
  <h3>Shopping Complex</h3>
  <p class="loc"><svg width="9" height="12" viewBox="0 0 9 12"><path d="M4.5 0A4.5 4.5 0 0 0 0 4.5C0 8 4.5 12 4.5 12S9 8 9 4.5A4.5 4.5 0 0 0 4.5 0z" fill="#222"/><circle cx="4.5" cy="4.5" r="1.6" fill="#fff"/></svg>Surat - Althan</p>
  <p class="view">› View the Listing</p>
</article>
<article class="abs card" style="left:603px;top:1070px">
  <div class="photo" role="img" aria-label="Photo of a tall golden tower against a blue sky" style="background:radial-gradient(ellipse 40px 150px at 132px 120px,rgba(210,170,90,.95),rgba(210,170,90,0)),radial-gradient(ellipse 120px 40px at 132px 230px,rgba(70,100,60,.7),rgba(70,100,60,0)),linear-gradient(180deg,#2e66a8 0%,#4f86c0 40%,#86aed4 70%,#7a7a68 100%)"><span class="name">Altus 24K</span></div>
  <h3>Shopping Complex</h3>
  <p class="loc"><svg width="9" height="12" viewBox="0 0 9 12"><path d="M4.5 0A4.5 4.5 0 0 0 0 4.5C0 8 4.5 12 4.5 12S9 8 9 4.5A4.5 4.5 0 0 0 4.5 0z" fill="#222"/><circle cx="4.5" cy="4.5" r="1.6" fill="#fff"/></svg>Gurgaon - Sohna Road</p>
  <p class="view">› View the Listing</p>
</article>
<article class="abs card" style="left:876px;top:1070px">
  <div class="photo" role="img" aria-label="Photo of a glass-fronted shopping mall with a canopy" style="background:radial-gradient(ellipse 130px 80px at 150px 130px,rgba(225,238,250,.9),rgba(225,238,250,0)),radial-gradient(ellipse 100px 40px at 132px 215px,rgba(60,130,90,.6),rgba(60,130,90,0)),linear-gradient(180deg,#3f86d0 0%,#7fb2e2 35%,#b8d4ec 60%,#6d7f92 100%)"><span class="name">Coral Mall</span></div>
  <h3>Shopping Complex</h3>
  <p class="loc"><svg width="9" height="12" viewBox="0 0 9 12"><path d="M4.5 0A4.5 4.5 0 0 0 0 4.5C0 8 4.5 12 4.5 12S9 8 9 4.5A4.5 4.5 0 0 0 4.5 0z" fill="#222"/><circle cx="4.5" cy="4.5" r="1.6" fill="#fff"/></svg>Gurgaon - Sohna Road</p>
  <p class="view">› View the Listing</p>
</article>

<!-- featured projects row 2 -->
<article class="abs card" style="left:60px;top:1491px">
  <div class="photo" role="img" aria-label="Photo of a colourful mall entrance with a blue skywalk sign" style="background:radial-gradient(ellipse 130px 40px at 132px 60px,rgba(40,120,220,.9),rgba(40,120,220,0)),radial-gradient(ellipse 140px 60px at 132px 130px,rgba(240,150,50,.85),rgba(240,150,50,0)),linear-gradient(180deg,#5d9ad6 0%,#3e7ac0 25%,#d88a3a 50%,#a06a40 72%,#58524c 100%)"><span class="name">Magnora</span></div>
  <h3>Shopping Complex</h3>
  <p class="loc"><svg width="9" height="12" viewBox="0 0 9 12"><path d="M4.5 0A4.5 4.5 0 0 0 0 4.5C0 8 4.5 12 4.5 12S9 8 9 4.5A4.5 4.5 0 0 0 4.5 0z" fill="#222"/><circle cx="4.5" cy="4.5" r="1.6" fill="#fff"/></svg>Surat - Althan</p>
  <p class="view">› View the Listing</p>
</article>
<article class="abs card" style="left:333px;top:1491px">
  <div class="photo" role="img" aria-label="Photo of a modern storefront building with red and white panels" style="background:radial-gradient(ellipse 60px 110px at 60px 140px,rgba(200,40,40,.85),rgba(200,40,40,0)),radial-gradient(ellipse 100px 100px at 180px 130px,rgba(240,240,240,.85),rgba(240,240,240,0)),linear-gradient(180deg,#6aa6e0 0%,#a9cbea 30%,#c8b8b0 55%,#8a8a8a 100%)"><span class="name">Vireo 81 High Street</span></div>
  <h3>Shopping Complex</h3>
  <p class="loc"><svg width="9" height="12" viewBox="0 0 9 12"><path d="M4.5 0A4.5 4.5 0 0 0 0 4.5C0 8 4.5 12 4.5 12S9 8 9 4.5A4.5 4.5 0 0 0 4.5 0z" fill="#222"/><circle cx="4.5" cy="4.5" r="1.6" fill="#fff"/></svg>Surat - Althan</p>
  <p class="view">› View the Listing</p>
</article>
<article class="abs card" style="left:603px;top:1491px">
  <div class="photo" role="img" aria-label="Photo of a mall facade with a large billboard at night" style="background:radial-gradient(ellipse 60px 80px at 110px 70px,rgba(200,170,150,.9),rgba(200,170,150,0)),radial-gradient(ellipse 140px 50px at 132px 200px,rgba(230,170,90,.7),rgba(230,170,90,0)),linear-gradient(180deg,#1c1c1e 0%,#3a3432 40%,#7a6050 65%,#3a3634 100%)"><span class="name">Altus 24K</span></div>
  <h3>Shopping Complex</h3>
  <p class="loc"><svg width="9" height="12" viewBox="0 0 9 12"><path d="M4.5 0A4.5 4.5 0 0 0 0 4.5C0 8 4.5 12 4.5 12S9 8 9 4.5A4.5 4.5 0 0 0 4.5 0z" fill="#222"/><circle cx="4.5" cy="4.5" r="1.6" fill="#fff"/></svg>Gurgaon - Sohna Road</p>
  <p class="view">› View the Listing</p>
</article>
<article class="abs card" style="left:876px;top:1491px">
  <div class="photo" role="img" aria-label="Photo of glass towers beside an elevated metro line" style="background:radial-gradient(ellipse 50px 130px at 180px 110px,rgba(70,110,150,.85),rgba(70,110,150,0)),radial-gradient(ellipse 140px 40px at 132px 200px,rgba(90,120,80,.7),rgba(90,120,80,0)),linear-gradient(180deg,#c4d8e8 0%,#a9c2d6 40%,#7f98ad 65%,#5e6a60 100%)"><span class="name">Coral Mall</span></div>
  <h3>Shopping Complex</h3>
  <p class="loc"><svg width="9" height="12" viewBox="0 0 9 12"><path d="M4.5 0A4.5 4.5 0 0 0 0 4.5C0 8 4.5 12 4.5 12S9 8 9 4.5A4.5 4.5 0 0 0 4.5 0z" fill="#222"/><circle cx="4.5" cy="4.5" r="1.6" fill="#fff"/></svg>Gurgaon - Sohna Road</p>
  <p class="view">› View the Listing</p>
</article>

<!-- mart wizards -->
<div class="abs wizards-photo" role="img" aria-label="Photo of glass office buildings at dusk"></div>
<div class="abs wizards-copy">
  <h2>Mart Wizards</h2>
  <p>Post your Retail Space requirement with us and our experts shall get back with suitable options and even help you in your transaction. This is a Free Service!</p>
  <div class="rule"></div>
</div>
<div class="abs wizards-form"></div>
<div class="abs in email">Enter Email</div>
<div class="abs in mobile">Mobile</div>
<div class="abs in message">Message</div>
<div class="abs send-btn">Send ›</div>

<!-- listing alert -->
<section class="abs info-box alert-box">
  <h2>— Listing Alert —</h2>
  <p class="lead">Subscribe for Fortnightly Email update on New Listings @ LotStallMart</p>
  <div class="box-field first" style="top:164px">Enter Email</div>
  <div class="box-field select" style="top:217px">Select Question</div>
  <p class="hint" style="top:258px">(select retail format of interest)</p>
  <div class="box-field select" style="top:291px">Select City</div>
  <p class="hint" style="top:332px">(select cities of interest)</p>
  <div class="box-btn" style="left:84px;top:391px;width:152px">Subscribe ›</div>
</section>

<!-- editor's choice -->
<section class="abs info-box editor-box">
  <h2>— Editor's Choice —</h2>
  <div class="pic" role="img" aria-label="Photo of a white office building under a blue sky"></div>
  <p class="copy">A "Select" Listing of Retail Properties Handpicked by our Editors based on their own positive evaluation on parameters &amp; attributes such as Design Concept, Location, Developer, Success Potential. So Read On to Check Out for yourself...</p>
  <div class="box-btn" style="left:116px;top:391px;width:99px">More ›</div>
</section>

<!-- footer -->
<footer class="abs footer" role="img" aria-label="Photo of shoppers walking along a busy city street"></footer>
<div class="abs footer-brand"><span class="dot"></span>lotstallmart</div>
<nav class="abs footer-links" style="top:3055px"><a class="hl">About Us</a><a>Privacy Policy</a><a>Terms of Use</a><a>Contact Us</a><a>Site Map</a></nav>
<nav class="abs footer-links" style="top:3088px"><a>Retail Malls</a><a>Shopping Complex</a><a>High Street Shops</a><a>Retail Warehouses</a></nav>
<div class="abs thumbs">
  <div class="thumb"><div class="pic" role="img" aria-label="Small photo of a mall" style="background:linear-gradient(180deg,#5d9ad6,#d88a3a 60%,#58524c)"></div>Lorem ipsum</div>
  <div class="thumb"><div class="pic" role="img" aria-label="Small photo of a shopping complex" style="background:linear-gradient(180deg,#8fbde4,#d6c29a 55%,#6e6a5a)"></div>Lorem ipsum</div>
  <div class="thumb"><div class="pic" role="img" aria-label="Small photo of a storefront" style="background:linear-gradient(90deg,#c83030,#eee 50%,#8a8a8a)"></div>Lorem ipsum</div>
  <div class="thumb"><div class="pic" role="img" aria-label="Small photo of a tower" style="background:linear-gradient(180deg,#2e66a8,#86aed4 60%,#7a7a68)"></div>Lorem ipsum</div>
  <div class="thumb"><div class="pic" role="img" aria-label="Small photo of a retail building" style="background:linear-gradient(180deg,#1f3358,#8a7458 60%,#4a4238)"></div>Lorem ipsum</div>
  <div class="thumb"><div class="pic" role="img" aria-label="Small photo of a warehouse" style="background:linear-gradient(180deg,#c4d8e8,#7f98ad 60%,#5e6a60)"></div>Lorem ipsum</div>
</div>
<div class="abs footer-bottom"></div>
<svg class="abs" style="left:88px;top:3388px" width="26" height="36" viewBox="0 0 9 12"><path d="M4.5 0A4.5 4.5 0 0 0 0 4.5C0 8 4.5 12 4.5 12S9 8 9 4.5A4.5 4.5 0 0 0 4.5 0z" fill="#fff"/><circle cx="4.5" cy="4.5" r="1.6" fill="#333"/></svg>
<address class="abs address">Unit 406, 4th Floor, Lorem Ipsum is simply, Sector x, Gurgaon - 122002<br>P: 000-000-0000 &nbsp;&nbsp; F: 000-000-0000</address>
<div class="abs socials"><i></i><i></i><i></i><i></i></div>
<p class="abs copyright">Copyright © 2015 Lotstall Ventures.com<br>All rights reserved</p>

</body>
</html>
```